Wordpress Powered Website. Outstanding Design Required. Using Morvenic Theme

Designers will not need to create anything other than the home page but there are some design elements on the home page which also need to be factored in: 6 product place holders and 2-3 slides for a slideshow (with images I provide).

Designers will need to familiarise themselves with the Morvenic theme to make sure that their design will work within the theme.

The winning designer will set up all the pages and navigation in place. This includes social media icons, favicon, widgets, etc. In other words, the home page needs to be designed and coded and the other preset theme pages need to be organised in a way that we can start using the website on completion of the job.

Most of the designs I had last time were too colourful. This needs to be subtle not in your face.

Background to the business/website:
Ridgeway Banners is a new Australian venture which will sell large format printed banners and other signage. The market is very competitive so it is important to stand out visually and to have a website which is clean, easy to navigate and easy to order. It will be a combination of online sales and assisted sales but all sales enquiries will come from the website.

As our business is focused on presentation it is vital to have excellent design.
Purchased theme is Morvenic. Only this theme is to be used.

1. A home page using all the preset features of the Morvenic theme - it will just be basically taking my wireframe and inputting it to the live theme.
2. A three slide slideshow, ideally with an edited video. The static image slides can be provided by me during the handover. Placeholder for now.
Similar to this one: http://thecedarhollow.example.au/

Attached is the logo which must be utilised, although it could also sit on a dark background. There is our mascot as well which can be used but does not have to be included.

Target Market(s)

Primarily B2B (business to business)
Main industries will be Construction, Retail, Community, Events & Trade Shows

Industry/Entity Type

Printing

Coding

Coded - Design and coding required

Font styles to use
Sans Serif

Requirements
Must have
• Must have the design files made to web pages within the Wordpress environment.
Nice to have
• Clean design. Stand out from competitors based on design.
Should not have
• Should not look like any competitor

```html
<!DOCTYPE html>
<html lang="en">
<head>
<meta charset="utf-8">
<title>Ridgeway Banners</title>
<link href="https://fonts.googleapis.com/css2?family=Open+Sans:ital,wght@0,400;0,600;0,700;1,700&family=Montserrat:wght@600;700&display=swap" rel="stylesheet">
<style>
:root{
  --black:#111111;
  --ink:#1d1d1d;
  --text:#333333;
  --muted:#666666;
  --white:#ffffff;
  --grey-band:#f2f2f2;
  --line:#dddddd;
  --blue:#1e73d2;
  --red:#e01f1f;
  --dark-circle:#3a3a3a;
  --green:#5c9a2a;
  --green-dark:#3f7a19;
  --brand:#1e73d2;
}
*{box-sizing:border-box;margin:0;padding:0}
html,body{width:1200px;height:3377px;overflow:hidden}
body{font-family:"Open Sans",Arial,sans-serif;color:var(--text);background:var(--white);position:relative}
.abs{position:absolute}
h2.section-title{font-family:"Montserrat",Arial,sans-serif;font-weight:700;font-size:24px;color:var(--ink);text-align:center;letter-spacing:.5px;position:absolute;left:0;width:1200px}
h2.section-title::after{content:"";display:block;width:220px;height:1px;background:var(--line);margin:12px auto 0}

/* top bar */
.topbar{top:0;left:0;width:1200px;height:36px;background:var(--black);color:var(--white);font-size:15px;font-weight:600}
.social{display:flex;gap:14px;position:absolute;top:11px;left:99px}
.social span{width:14px;height:14px;border-radius:50%;background:var(--white);display:block}
.topbar .contact{position:absolute;right:99px;top:7px;display:flex;gap:28px;align-items:center}
.topbar .contact div{display:flex;align-items:center;gap:8px}

/* header */
.header{top:36px;left:0;width:1200px;height:83px;background:var(--white)}
.logo{position:absolute;left:99px;top:22px;font-family:"Open Sans",Arial,sans-serif;font-weight:700;font-size:30px;color:var(--brand);line-height:1}
.logo small{display:block;font-size:13px;letter-spacing:3px;margin-top:4px}
.nav{position:absolute;right:99px;top:33px;display:flex;gap:0}
.nav a{font-size:13px;font-weight:600;color:var(--ink);text-decoration:none;letter-spacing:.5px;padding:0 32px;border-left:1px solid var(--line)}
.nav a:first-child{border-left:none}
.nav a:last-child{padding-right:0}

/* hero */
.hero{top:119px;left:0;width:1200px;height:428px;overflow:hidden;background:linear-gradient(120deg,#5a4630 0%,#8a6c44 35%,#c59a55 60%,#6d5538 100%)}
.hero-shade{position:absolute;inset:0;background:rgba(0,0,0,.35)}
.hero h1{position:absolute;left:99px;top:148px;width:500px;color:var(--white);font-size:23px;font-weight:700;line-height:34px}
.hero .btn{position:absolute;left:99px;top:262px;width:149px;height:34px;background:var(--black);color:var(--white);font-size:14px;font-weight:700;display:flex;align-items:center;justify-content:center}
.dots{position:absolute;left:99px;top:394px;display:flex;gap:8px}
.dots span{width:12px;height:12px;border-radius:50%;border:2px solid var(--white)}
.dots span.on{background:var(--white)}
.bubble{position:absolute;border-radius:50%;border:4px solid var(--white)}
.brand-bubble{position:absolute;left:833px;top:167px;width:90px;height:90px;border-radius:50%;background:var(--white);display:flex;align-items:center;justify-content:center;text-align:center;font-weight:700;font-size:12px;color:var(--brand);line-height:14px}

/* products */
.tile{position:absolute;width:300px;height:205px;display:flex;align-items:center;justify-content:center;color:var(--white);font-weight:700;font-size:18px;letter-spacing:.5px}
.tile::before{content:"";position:absolute;inset:0;background:rgba(0,0,0,.35)}
.tile span{position:relative}

/* difference */
.difference{top:1150px;left:0;width:1200px;height:412px;background:var(--grey-band)}
.feature{position:absolute;top:131px;width:240px;text-align:center}
.feature .icon{width:110px;height:110px;border-radius:50%;background:var(--blue);margin:0 auto;display:flex;align-items:center;justify-content:center}
.feature h3{font-size:14px;font-weight:600;color:var(--ink);margin-top:24px;letter-spacing:.3px}
.feature p{font-size:12px;line-height:20px;color:var(--text);margin-top:22px}

/* process */
.step{position:absolute;top:1689px;width:250px;text-align:center}
.step .ring{width:134px;height:134px;border-radius:50%;border:4px solid var(--red);margin:0 auto;display:flex;align-items:center;justify-content:center;background:var(--dark-circle);box-shadow:0 6px 10px rgba(0,0,0,.15)}
.step h3{font-size:13px;font-weight:700;color:var(--ink);margin-top:26px;letter-spacing:.3px}
.connector{position:absolute;top:1748px;display:flex;gap:12px;align-items:center}
.connector span{border-radius:50%;background:#e3e3e3}

/* latest work */
.work-band{top:1902px;left:0;width:1200px;height:113px;background:var(--grey-band)}
.work{position:absolute;top:2015px;left:0;width:1200px;height:416px;background:#ddd}
.work div{position:absolute;border:1px solid var(--white)}
.work .caption{display:flex;align-items:center;justify-content:center;text-align:center;color:var(--white);font-weight:700;font-size:16px;line-height:22px;background:#3b3b3b}

/* about */
.about-title{top:2478px}
.about h3{position:absolute;left:99px;top:2560px;font-size:15px;font-weight:700;color:var(--ink)}
.about p{position:absolute;left:99px;width:682px;font-size:13px;line-height:20px;color:var(--text)}

/* quote */
.quote{top:2870px;left:0;width:1200px;height:277px;background:linear-gradient(100deg,#c7b7a2 0%,#e8d6c8 30%,#f2dfd6 55%,#cfc8c0 80%,#b9c4ab 100%)}
.quote h2{position:absolute;top:43px;left:0;width:1200px;text-align:center;color:var(--white);font-size:24px;font-weight:700}
.field{position:absolute;background:var(--white);font-size:11px;color:#555;padding:6px 8px}
.submit{position:absolute;left:549px;top:199px;width:99px;height:33px;background:var(--red);color:var(--white);font-weight:700;font-size:15px;display:flex;align-items:center;justify-content:center}

/* support band */
.support{top:3147px;left:0;width:1200px;height:163px;background:linear-gradient(180deg,var(--green) 0%,var(--green-dark) 100%);color:var(--white)}
.support h2{position:absolute;top:28px;left:0;width:1200px;text-align:center;font-size:25px;font-weight:700;font-style:italic}
.help{position:absolute;top:86px;display:flex;gap:14px;align-items:flex-start}
.help b{display:block;font-size:17px;font-style:italic;font-weight:700}
.help span{display:block;font-size:13px;opacity:.85;font-style:italic}

/* footer */
.footer{top:3310px;left:0;width:1200px;height:67px;background:var(--black);color:var(--white);font-size:12px;font-weight:700}
.footer .links{position:absolute;left:99px;top:25px;letter-spacing:.5px}
.footer .social{left:543px;top:26px}
.footer .copy{position:absolute;right:99px;top:25px;font-weight:600}
</style>
</head>
<body>

<header class="abs topbar">
  <div class="social"><span></span><span></span><span></span><span></span><span></span></div>
  <div class="contact">
    <div><svg width="18" height="13" viewBox="0 0 18 13"><rect width="18" height="13" fill="#fff"/><path d="M0 0 L9 7 L18 0" stroke="#111" stroke-width="1.5" fill="none"/></svg>info@ridgewaybanners.example</div>
    <div><svg width="14" height="14" viewBox="0 0 24 24"><path fill="#fff" d="M6.6 10.8a15 15 0 0 0 6.6 6.6l2.2-2.2a1 1 0 0 1 1-.25 11.4 11.4 0 0 0 3.6.57 1 1 0 0 1 1 1V20a1 1 0 0 1-1 1A17 17 0 0 1 3 4a1 1 0 0 1 1-1h3.5a1 1 0 0 1 1 1c0 1.25.2 2.45.57 3.57a1 1 0 0 1-.25 1z"/></svg>123-456-7890</div>
  </div>
</header>

<div class="abs header">
  <div class="logo">Ridgeway<small>BANNERS</small></div>
  <nav class="nav"><a>PRODUCTS</a><a>GET A QUOTE</a><a>CONTACT US</a></nav>
</div>

<section class="abs hero" role="img" aria-label="Slideshow photo of a print workshop floor with printed banners being prepared">
  <div class="hero-shade"></div>
  <h1>We Are A New Australian Firm Which Will Sell Large Format Printed Banners And Other Signage Material</h1>
  <div class="btn">CONACT NOW !</div>
  <div class="dots"><span></span><span class="on"></span><span></span><span></span></div>
  <div class="bubble" role="img" aria-label="Photo of a person holding a printed banner" style="left:663px;top:60px;width:150px;height:150px;background:linear-gradient(135deg,#6b8a4a,#3d4f2d)"></div>
  <div class="bubble" role="img" aria-label="Photo of retail store signage" style="left:884px;top:4px;width:210px;height:210px;background:linear-gradient(135deg,#d8e4f0,#2f6fb5)"></div>
  <div class="bubble" role="img" aria-label="Photo of colourful printed flags" style="left:672px;top:222px;width:200px;height:200px;background:linear-gradient(135deg,#c22a2a,#e2b93b,#2a4a8a)"></div>
  <div class="bubble" role="img" aria-label="Photo of a large event banner on a building" style="left:889px;top:205px;width:214px;height:214px;background:linear-gradient(135deg,#c9c6c0,#b3312c)"></div>
  <div class="brand-bubble">Ridgeway<br>Banners</div>
</section>

<h2 class="section-title" style="top:588px">OUR PRODUCTS</h2>
<div class="tile" role="img" aria-label="Photo of banner and fabric printing" style="left:99px;top:660px;background:linear-gradient(135deg,#7a4a22,#b5773a)"><span>BANNERS &amp; FABRICS</span></div>
<div class="tile" role="img" aria-label="Photo of printed boards and signs" style="left:449px;top:660px;background:linear-gradient(135deg,#c9c2bd,#8c3b3b)"><span>BOARDS &amp; SIGNS</span></div>
<div class="tile" role="img" aria-label="Photo of feather flags on a beach" style="left:800px;top:660px;background:linear-gradient(135deg,#4e8fb8,#c4a06a)"><span>FLAGS &amp; POS</span></div>
<div class="tile" role="img" aria-label="Photo of a self adhesive vinyl print" style="left:99px;top:903px;background:linear-gradient(135deg,#7a8a3a,#e0a030)"><span>SELF ADHESIVE VINYLS</span></div>
<div class="tile" role="img" aria-label="Photo of pull up banners in a room" style="left:449px;top:903px;background:linear-gradient(135deg,#6a6a6a,#b8b2aa)"><span>PULL UP BANNERS</span></div>
<div class="tile" role="img" aria-label="Photo of printed posters on a desk" style="left:800px;top:903px;background:linear-gradient(135deg,#7a3a22,#c9a88a)"><span>POSTERS</span></div>

<section class="abs difference">
  <h2 class="section-title" style="top:40px">OUR DIFFERENCE</h2>
  <div class="feature" style="left:123px">
    <div class="icon"><svg width="50" height="50" viewBox="0 0 50 50"><circle cx="20" cy="20" r="12" stroke="#fff" stroke-width="5" fill="none"/><path d="M29 29 L42 42" stroke="#fff" stroke-width="7" stroke-linecap="round"/></svg></div>
    <h3>Attention To Detail</h3>
    <p>Lorem ipsum dolor sit amet, consectetur adipiscing elit. Aenean et dignissim sem, interdum risus.</p>
  </div>
  <div class="feature" style="left:350px">
    <div class="icon"><svg width="50" height="50" viewBox="0 0 50 50"><circle cx="25" cy="25" r="15" stroke="#fff" stroke-width="4" fill="none"/><circle cx="25" cy="25" r="5" fill="#fff"/><path d="M25 3v9M25 38v9M3 25h9M38 25h9" stroke="#fff" stroke-width="4"/></svg></div>
    <h3>FAST AND FLEXIBLE</h3>
    <p>Lorem ipsum dolor sit amet, consectetur adipiscing elit. Aenean et dignissim sem, interdum risus.</p>
  </div>
  <div class="feature" style="left:607px">
    <div class="icon"><svg width="50" height="50" viewBox="0 0 50 50"><rect x="6" y="22" width="9" height="20" fill="#fff"/><path d="M18 22 L26 8 Q31 8 30 15 L29 20 H40 Q44 21 43 25 L39 40 Q38 42 35 42 H18 Z" fill="#fff"/></svg></div>
    <h3>SECURE DELIVERY</h3>
    <p>Lorem ipsum dolor sit amet, consectetur adipiscing elit. Aenean et dignissim sem, interdum risus.</p>
  </div>
  <div class="feature" style="left:868px">
    <div class="icon"><svg width="50" height="50" viewBox="0 0 50 50"><path d="M16 14 H34 L38 44 H12 Z" fill="#fff"/><path d="M19 16 V10 Q25 3 31 10 V16" stroke="#fff" stroke-width="3" fill="none"/><text x="25" y="37" text-anchor="middle" font-family="Open Sans,sans-serif" font-weight="700" font-size="14" fill="#1e73d2">$</text></svg></div>
    <h3>NICE PRICES</h3>
    <p>Lorem ipsum dolor sit amet, consectetur adipiscing elit. Aenean et dignissim sem, interdum risus.</p>
  </div>
</section>

<h2 class="section-title" style="top:1604px">OUR PROCESS</h2>
<div class="step" style="left:161px">
  <div class="ring"><svg width="46" height="46" viewBox="0 0 46 46"><rect x="6" y="8" width="28" height="30" stroke="#fff" stroke-width="3" fill="none"/><path d="M18 23 H40 M33 16 L40 23 L33 30" stroke="#fff" stroke-width="4" fill="none"/></svg></div>
  <h3>LOREM IPSUM SIT DOLOR</h3>
</div>
<div class="connector" style="left:388px"><span style="width:8px;height:8px"></span><span style="width:12px;height:12px"></span><span style="width:18px;height:18px"></span><span style="width:24px;height:24px"></span></div>
<div class="step" style="left:476px">
  <div class="ring"><svg width="46" height="46" viewBox="0 0 46 46"><rect x="9" y="7" width="28" height="34" rx="2" stroke="#fff" stroke-width="3" fill="none"/><rect x="17" y="4" width="12" height="7" fill="#fff"/><path d="M15 20h16M15 27h16M15 34h10" stroke="#fff" stroke-width="3"/></svg></div>
  <h3>LOREM IPSUM SIT DOLOR</h3>
</div>
<div class="connector" style="left:700px"><span style="width:8px;height:8px"></span><span style="width:12px;height:12px"></span><span style="width:18px;height:18px"></span><span style="width:24px;height:24px"></span></div>
<div class="step" style="left:787px">
  <div class="ring"><svg width="46" height="46" viewBox="0 0 46 46"><path d="M8 6 H26 L32 12 V40 H8 Z" fill="#fff"/><path d="M20 25 H42 M35 18 L42 25 L35 32" stroke="#3a3a3a" stroke-width="6" fill="none"/><path d="M20 25 H42 M35 18 L42 25 L35 32" stroke="#fff" stroke-width="3" fill="none"/></svg></div>
  <h3>LOREM IPSUM SIT DOLOR</h3>
</div>

<div class="abs work-band"><h2 class="section-title" style="top:40px">OUR LATEST WORK</h2></div>
<section class="work">
  <div role="img" aria-label="Photo of printed banners in a shopfront" style="left:0;top:0;width:196px;height:120px;background:linear-gradient(135deg,#b07a4a,#d8c2a0)"></div>
  <div role="img" aria-label="Photo of a designer working on a layout" style="left:196px;top:0;width:196px;height:208px;background:linear-gradient(135deg,#3a6fa8,#dfe6ee)"></div>
  <div role="img" aria-label="Photo of pull up banners at an expo" style="left:392px;top:0;width:196px;height:285px;background:linear-gradient(135deg,#5a5a6a,#d9d2c8)"></div>
  <div role="img" aria-label="Photo of printed brochures" style="left:588px;top:0;width:222px;height:130px;background:linear-gradient(135deg,#8a3a3a,#c9c0b8)"></div>
  <div role="img" aria-label="Photo of a large printed poster with numbers" style="left:810px;top:0;width:194px;height:208px;background:linear-gradient(135deg,#f0f0f0,#b7282b)"></div>
  <div role="img" aria-label="Photo of event signage boards outdoors" style="left:1004px;top:0;width:196px;height:120px;background:linear-gradient(135deg,#2a3a2a,#7a8a6a)"></div>
  <div role="img" aria-label="Photo of colourful printed flyers" style="left:0;top:120px;width:196px;height:176px;background:linear-gradient(135deg,#e8d02a,#c22a8a)"></div>
  <div role="img" aria-label="Photo of a fashion billboard print" style="left:196px;top:208px;width:196px;height:208px;background:linear-gradient(135deg,#c89a7a,#6a5a8a)"></div>
  <div class="caption" style="left:588px;top:130px;width:222px;height:286px">LOREM IPSUM<br>DOLOR SIT AMET</div>
  <div role="img" aria-label="Photo of printed flags in sunlight" style="left:810px;top:208px;width:194px;height:208px;background:linear-gradient(135deg,#e8b83a,#c23a2a)"></div>
  <div role="img" aria-label="Photo of sale posters on a wall" style="left:1004px;top:120px;width:196px;height:176px;background:linear-gradient(135deg,#f2f2f2,#d02a2a)"></div>
  <div role="img" aria-label="Photo of a stack of printed cards" style="left:1004px;top:296px;width:196px;height:120px;background:linear-gradient(135deg,#e8efe8,#2a8a6a)"></div>
  <div role="img" aria-label="Photo of printed menu boards" style="left:0;top:296px;width:196px;height:120px;background:linear-gradient(135deg,#8ac23a,#e8d85a)"></div>
  <div role="img" aria-label="Photo of an infographic print" style="left:392px;top:285px;width:196px;height:131px;background:linear-gradient(135deg,#2a8aa8,#e85a5a)"></div>
</section>

<section class="about">
  <h2 class="section-title about-title">ABOUT RIDGEWAY BANNERS</h2>
  <h3>OUR LITTLE BUSINESS</h3>
  <p style="top:2586px">Lorem ipsum dolor sit amet, consectetur adipiscing elit. Aenean et dignissim sem, interdum risus. Vestibulum consectetur nisi mollis diam pulvinar adipiscing. Vestibulum ut urna nec nibh adipiscing facilisis. Etiam auctor porta lacus ac luctus. Praesent ac libero fermentum, rhoncus magna a, dapibus mauris. Nam ut auctor justo. Sed ante odio, luctus quis nequ nec, adipiscing eleifend arcu. Integer nunc turpis, porttitor at lorem ut.Quisque hendrerit Lorem ipsum dolor sit amet, consectetur adipiscing elit. Aenean et dignissim sem, interdum risus. Vestibulum consectetur nisi mollis diam pulvinar adipiscing. Vestibulum ut urna nec nibh adipiscing facilisis. Etiam auctor porta lacus ac luctus. Praesent ac libero fermentum, rhoncus magna a, dapibus mauris.</p>
  <p style="top:2752px">Lorem ipsum dolor sit amet, consectetur adipiscing elit. Aenean et dignissim sem, interdum risus. Vestibulum consectetur nisi mollis diam pulvinar adipiscing. Vestibulum ut urna nec nibh adipiscing facilisis. Etiam auctor porta lacus ac luctus. Praesent ac libero fermentum, rhoncus magna a, dapibus mauris.</p>
  <div class="abs" role="img" aria-label="Photo of a staff member at a computer in the office" style="left:837px;top:2560px;width:264px;height:130px;background:linear-gradient(135deg,#e8ecf0,#3a4a8a)"></div>
  <div class="abs" role="img" aria-label="Photo of the business team" style="left:837px;top:2704px;width:264px;height:130px;background:linear-gradient(135deg,#f0f0f0,#2a2a35)"></div>
</section>

<section class="abs quote" role="img" aria-label="Soft blurred background photo behind the quote form">
  <h2>GET A QUOTE</h2>
  <div class="field" style="left:171px;top:113px;width:214px;height:32px">Name</div>
  <div class="field" style="left:398px;top:113px;width:214px;height:32px">Email</div>
  <div class="field" style="left:633px;top:113px;width:396px;height:70px">Your Message</div>
  <div class="field" style="left:171px;top:151px;width:214px;height:32px">Phone Number</div>
  <div class="field" style="left:398px;top:151px;width:214px;height:32px">Enquiry Type<svg style="position:absolute;right:8px;top:12px" width="10" height="6" viewBox="0 0 10 6"><path d="M0 0 L5 6 L10 0Z" fill="#888"/></svg></div>
  <div class="submit">SUBMIT</div>
</section>

<section class="abs support">
  <h2>We're Dedicated to Our Customers 24x7</h2>
  <div class="help" style="left:99px"><svg width="38" height="38" viewBox="0 0 24 24"><path fill="#fff" d="M6.6 10.8a15 15 0 0 0 6.6 6.6l2.2-2.2a1 1 0 0 1 1-.25 11.4 11.4 0 0 0 3.6.57 1 1 0 0 1 1 1V20a1 1 0 0 1-1 1A17 17 0 0 1 3 4a1 1 0 0 1 1-1h3.5a1 1 0 0 1 1 1c0 1.250.2 2.450.57 3.57a1 1 0 0 1-.25 1z"/></svg><div><b>123-456-7890</b><span>Available 24/7 - Call us any time.</span></div></div>
  <div class="help" style="left:417px"><svg width="44" height="34" viewBox="0 0 44 34"><rect x="2" y="2" width="40" height="30" stroke="#fff" stroke-width="3" fill="none"/><path d="M2 2 L22 19 L42 2" stroke="#fff" stroke-width="3" fill="none"/></svg><div><b>Email Us</b><span>Have a question? Let us help.</span></div></div>
  <div class="help" style="left:724px"><svg width="42" height="36" viewBox="0 0 42 36"><path d="M4 4h22v14H12l-6 5v-5H4z" stroke="#fff" stroke-width="3" fill="none"/><path d="M18 22h10l6 5v-5h4V10h-8" stroke="#fff" stroke-width="3" fill="none"/></svg><div><b>Live Chat</b><span>Online Support</span></div></div>
  <div class="help" style="left:932px"><svg width="26" height="38" viewBox="0 0 26 38"><path d="M4 11a9 9 0 1 1 13 8c-3 2-4 3-4 7" stroke="#fff" stroke-width="5" fill="none"/><circle cx="13" cy="34" r="3.5" fill="#fff"/></svg><div><b>Help</b><span>Find your answers.</span></div></div>
</section>

<footer class="abs footer">
  <div class="links">PRODUCTS &nbsp;/&nbsp; GET A QUOTE &nbsp;/&nbsp; CONTACT US</div>
  <div class="social"><span></span><span></span><span></span><span></span><span></span></div>
  <div class="copy">© 2016 RIDGEWAY BANNERS. ALL RIGHTS RESERVED.</div>
</footer>

</body>
</html>
```